Fantasy Football UX Style Guide & Sample Pages (QWR - not soccer)

Happy April designers!! We are looking to establish a relationship with a killer designer who can work with us on establishing an exciting, professional UX that is delivers a great experience and leverages the powerful technologies of react.js and other 2015 advancements.

Our ideal design team can be one or more people -- but is responsive to feedback, has "no ego" in his/her designs and is willing to go the extra mile to get the job done well. We expect several iterations before any design is considered final. If this excites you - jump in!! If you think working together in an iterative fashion would frustrate you -- please stop now. We will give lots of feedback and ideas. The UX resulting is very important to us.

The site that we are building is related to QWR football. If you have no experience watching American QWR Football -- please stop reading. If you enjoy this game and would like to design UX elements that have an affinity -- please join this design contest.

As a starter project -- we are going to ask that someone review the designs that we have received for a variety of project design competitions. You will notice that they are all pretty disjointed (from our opinion) and also a little 2005 from a design perspective. The winner from this competition will assemble an accepted, killer design that will bring all of these "pages" together into a common design. We would like to see each page in the concept.

Ultimately, what this amounts to is a common style guide that delivers on the strength of the existing brand & logo (files 1 & 2) --- and hopefully -- takes it, and the pages to the next level.

Please note: While our ideal partner will give us an iteration of each page in the new design style guide -- the style guide itself is what is the most important deliverable. We won't expect every page to be perfect. We realize that will take some additional project work.

Target Market(s)

fantasy sports players

Industry/Entity Type

Work

Number of Pages Required

5+ page

Font styles to use
Serif
Sans Serif

Colors
ec1f27
ffffff
161616
959595

Requirements
Must have
• Must Have:
• - A strong sense of brand (please feel free to ask questions; logo is in file 1 & 2)
• - A strong understanding of what resonates with fantasy football players
• - A STYLE GUIDE -- I mention this above but this our primary deliverable for this project. We are looking for an awesome style guide that can be used to deliver any page / mobile app regardless of what is on it. [file attached for example of what a proper style guide looks like. We would like to see this expanded upon]
• - We are looking to see the style guide applied to a variety of page types (examples are shared in the files below -- home page, blog home page, blog item page, specific pages of importance.) This will give us a sense of how the style guide holds up and if we need some new areas addressed in it.
• - We recognize that each page doesn't have to be pixel perfect, and we are willing to take that on as additional project work if the designer would like it.
• - An design that is "easy to read" but conveys excitement
• - We deal with a lot of "sports analytics" so understanding what makes for a good chart is helpful. (if you want to use examples from d3, that is even better)
• - An understanding for how to visualize date & trends in data (see above)
• - A modern REACT.JS like look; not looking for styles from 10 years ago
Nice to have
• - Fresh new takes on the layouts included here.
• - Suggestions for how to make the logo more 2015
• - Creative, visionary ideas
• - Questions for what the screens attached are meant to portray (we'd rather you ask)
Should not have
• - A new logo or color palette. We like what we have and have an established presence here.
• - We are looking for pure, kick-ass design at this point. We don't want it coded.
• - There are many elements that we like from the concept pages below. You don't have to redesign everything. What we don't like is that the UX is not great, and there is no common styling. Also the design itself feels a little "dated" and "dark" in some areas. We are hoping for something more exciting and fresh.

```html
<!DOCTYPE html>
<html lang="en">
<head>
<meta charset="utf-8">
<title>Endzone Oracle – Home</title>
<link href="https://fonts.googleapis.com/css2?family=Open+Sans:ital,wght@0,400;0,600;0,700;1,400&family=Play:wght@400;700&display=swap" rel="stylesheet">
<style>
:root{
  --red:#d3202a;
  --red-dark:#a9121b;
  --red-text:#e0232b;
  --ink:#161616;
  --grey:#959595;
  --text:#333333;
  --line:#e3e3e3;
  --card:#f7f7f7;
  --white:#ffffff;
  --footer:#121212;
}
*{box-sizing:border-box;margin:0;padding:0}
html,body{width:1200px;height:2571px;overflow:hidden}
body{position:relative;background:var(--white);font-family:"Open Sans",Arial,sans-serif;color:var(--text)}
.photo{position:absolute;overflow:hidden}

/* header */
.site-header{position:absolute;left:0;top:0;width:1200px;height:142px;background:linear-gradient(100deg,#b6121c 0%,#d21d27 45%,#c01620 100%)}
.brand{position:absolute;left:98px;top:34px;height:66px;display:flex;align-items:center;gap:14px}
.brand-mark{width:66px;height:66px;background:#9e0f18}
.brand-name{font-family:"Play",sans-serif;font-weight:700;color:var(--white);font-size:33px;line-height:1}
.top-links{position:absolute;left:590px;top:73px;font-size:12px;color:var(--white);letter-spacing:.5px}
.top-links span{margin:0 6px}
.btn-dark{position:absolute;top:65px;height:31px;background:#1e1e1e;color:var(--white);font-size:14px;line-height:31px;text-align:center;border-radius:2px}

.main-nav{position:absolute;left:0;top:142px;width:1200px;height:55px;background:linear-gradient(#2a2a2a,#1a1a1a)}
.main-nav a{position:absolute;top:0;height:55px;line-height:55px;color:var(--white);font-size:13px;text-decoration:none;letter-spacing:.3px}
.main-nav .active{background:var(--red);left:98px;width:96px;text-align:center}

/* hero */
.hero{position:absolute;left:98px;top:218px;width:1002px;height:480px;box-shadow:0 14px 18px -12px rgba(0,0,0,.45)}
.top-stories{position:absolute;left:737px;top:0;width:265px;height:480px;background:rgba(25,25,25,.88)}
.top-stories h2{height:53px;background:var(--red-dark);color:var(--white);font-family:"Play",sans-serif;font-weight:400;font-size:21px;line-height:53px;padding-left:28px}
.top-stories ul{list-style:none;padding:10px 25px 0 26px}
.top-stories li{color:var(--white);font-size:12.5px;line-height:20px;padding:10px 0;border-bottom:1px solid rgba(255,255,255,.12)}
.top-stories li:last-child{border-bottom:none}
.slide-arrows{position:absolute;right:0;bottom:0;display:flex}
.slide-arrows span{width:28px;height:27px;display:flex;align-items:center;justify-content:center}

/* section titles */
.section-title{position:absolute;font-family:"Play",sans-serif;font-weight:400;font-size:21px;color:var(--ink)}
.side-title{position:absolute;left:828px;width:272px;font-family:"Play",sans-serif;font-weight:400;font-size:19px;color:var(--ink);padding-bottom:12px;border-bottom:1px solid var(--line)}
.side-title::after{content:"";position:absolute;left:0;bottom:-1px;width:40px;height:2px;background:var(--red)}

/* blog cards */
.blog-card{position:absolute;left:98px;width:699px;height:262px;background:var(--card);border:1px solid var(--line)}
.blog-card .photo{left:21px;top:21px;width:283px;height:216px}
.blog-body{position:absolute;left:331px;top:15px;width:345px}
.blog-body h3{font-family:"Play",sans-serif;font-weight:400;font-size:19px;color:var(--red-text);letter-spacing:.3px}
.meta{display:flex;align-items:center;margin-top:14px;font-size:12px;font-style:italic;color:#555}
.meta span{display:flex;align-items:center;gap:6px}
.meta .sep{width:1px;height:13px;background:#ccc;margin:0 14px}
.blog-body p{font-size:11.5px;line-height:20px;color:#444;margin-top:12px}
.cats{font-size:11px;color:#333;margin-top:13px}
.cats b{color:var(--red-text);font-size:13px;font-weight:600;margin-right:6px}
.more{font-size:12.5px;color:var(--ink);margin-top:14px;font-weight:600}

/* featured video */
.video-main{position:absolute;left:98px;top:1964px;width:337px;height:263px}
.video-caption{position:absolute;left:0;bottom:0;width:100%;height:52px;background:rgba(0,0,0,.55);color:var(--white);font-size:13px;line-height:52px;text-align:center}
.video-thumb{position:absolute;width:159px;height:105px}
.thumb-cap{position:absolute;font-size:11.5px;color:#333;width:165px;white-space:nowrap}

/* sidebar lists */
.news-item{position:absolute;left:828px;width:272px}
.news-item .photo{left:0;top:0;width:92px;height:72px}
.news-item .nt{position:absolute;left:107px;top:0;font-size:14px;color:var(--ink)}
.news-item .nd{position:absolute;left:107px;top:26px;width:165px;font-size:11.5px;line-height:18px;color:#555}
.off-item{position:absolute;left:828px;width:272px;height:86px;border-top:1px solid var(--line)}
.off-item .photo{left:0;top:13px;width:92px;height:66px}
.off-item .nd{position:absolute;left:107px;top:10px;width:150px;font-size:11.5px;line-height:18px;color:#444}

.ad{position:absolute;left:828px;width:272px}
.social-btn{position:absolute;top:2160px;width:62px;height:60px;color:var(--white);font-size:10.5px;text-align:center;padding-top:10px}
.social-btn i{display:block;width:26px;height:26px;border:2px solid var(--white);border-radius:50%;margin:0 auto 4px}

/* footer */
.site-footer{position:absolute;left:0;top:2292px;width:1200px;height:279px;background:var(--footer);color:#9a9a9a}
.f-col{position:absolute;top:38px}
.f-col h4{font-family:"Play",sans-serif;font-weight:400;font-size:17px;color:#d0d0d0;margin-bottom:18px;letter-spacing:.5px}
.f-col p{font-size:11.5px;line-height:20px}
.contact-row{display:flex;align-items:center;gap:16px;font-size:12.5px;margin-top:10px;color:#bbb}
.newsletter{display:flex;margin-top:22px}
.newsletter input{width:180px;height:38px;background:#121212;border:none;color:#666;font-size:11px;padding-left:14px;font-family:inherit}
.newsletter button{width:82px;height:38px;background:var(--red);border:none;color:var(--white);font-size:16px;font-family:"Play",sans-serif}
.social-list{list-style:none}
.social-list li{display:flex;align-items:center;gap:14px;font-size:12.5px;line-height:28px;color:#bbb}
.social-list i{width:8px;height:8px;border-radius:50%;background:#bbb;display:block}
.f-rule{position:absolute;left:98px;top:218px;width:1002px;height:1px;background:#262626}
.copyright{position:absolute;left:0;top:242px;width:1200px;text-align:center;font-size:12px;color:#ccc}
</style>
</head>
<body>

<header class="site-header">
  <div class="brand">
    <div class="brand-mark"></div>
    <span class="brand-name">Endzone Oracle</span>
  </div>
  <div class="top-links">WEEKLY RANKINGS<span>/</span>QWR TEAMS<span>/</span>PRESEASON</div>
  <div class="btn-dark" style="left:908px;width:79px">LOGIN</div>
  <div class="btn-dark" style="left:1003px;width:97px">REGISTER</div>
</header>

<nav class="main-nav">
  <a class="active">HOME</a>
  <a style="left:226px">LATEST ARTICLES</a>
  <a style="left:401px">FANTASY FOOTBALL NEWS</a>
  <a style="left:638px">FANTASY FOOTBALL ADVICE</a>
  <a style="left:887px">CONTACT US</a>
</nav>

<section class="hero">
  <div class="photo" role="img" aria-label="Football player in red number 29 jersey crouched at the line of scrimmage" style="left:0;top:0;width:737px;height:480px;background:linear-gradient(180deg,#3b2f2e 0%,#6a3b32 35%,#8a2a2c 55%,#4f6a3a 80%,#3f5a2d 100%)"></div>
  <aside class="top-stories">
    <h2>TOP STORIES</h2>
    <ul>
      <li>2014 QWR Free Agent WRs Rising &amp; Falling on New Teams RBS</li>
      <li>Nate Folsom Getting Plenty of Love in Early Rankings</li>
      <li>Fantasy Football Rookies: Position Review for WRs scoring NBS</li>
      <li>Marcus Flood out for fantasy Title Game week WR Players</li>
      <li>Tebbins' QWR comeback workouts are exhausting falling breakzes 2014</li>
      <li>Falling on New Teams RBS Jay Patton sues Keystone State over Sandler</li>
    </ul>
    <div class="slide-arrows">
      <span style="background:var(--red-dark)"><svg width="8" height="12" viewBox="0 0 8 12"><path d="M6 1 1 6l5 5" fill="none" stroke="#fff" stroke-width="2"/></svg></span>
      <span style="background:#2b2b2b"><svg width="8" height="12" viewBox="0 0 8 12"><path d="m2 1 5 5-5 5" fill="none" stroke="#fff" stroke-width="2"/></svg></span>
    </div>
  </aside>
</section>

<h2 class="section-title" style="left:98px;top:730px">LATEST BLOG</h2>

<article class="blog-card" style="top:773px">
  <div class="photo" role="img" aria-label="Teams lined up on the field before the snap" style="background:linear-gradient(180deg,#3a3a3a 0%,#5d6b55 35%,#5a8a3e 65%,#4a7a33 100%)"></div>
  <div class="blog-body">
    <h3>FANTASY FOOTBALL</h3>
    <div class="meta"><span><svg width="12" height="12" viewBox="0 0 12 12"><rect x="1" y="2" width="10" height="9" fill="none" stroke="#555"/><path d="M1 5h10" stroke="#555"/></svg>March 25, 2015</span><i class="sep"></i><span><svg width="12" height="12" viewBox="0 0 12 12"><path d="M1 2h10v6H5l-3 3V8H1z" fill="none" stroke="#555"/></svg>No comments</span><i class="sep"></i><span><svg width="12" height="12" viewBox="0 0 12 12"><path d="M2 10 9 3l1 1-7 7H2z" fill="#555"/></svg>Makeup</span></div>
    <p>Lorem ipsum dolor sit amet, consectetur adipiscing elit, sed do eiusmod tempor incididunt ut labore et dolore magna aliqua. Ut enim ad minim veniam, quis nostrud exercitation ullamco laboris nisi ut aliquip ex ea commodo consequat. r</p>
    <div class="cats"><b>CATEGORIES :</b>Fantasy football , World's Worst , ween, wellhead</div>
    <div class="more">CLICK HERE &gt;&gt;</div>
  </div>
</article>

<article class="blog-card" style="top:1056px">
  <div class="photo" role="img" aria-label="Referee standing beside a football on the grass" style="background:linear-gradient(180deg,#5a2a2a 0%,#8a3a3a 40%,#6f7a5a 70%,#4f7c37 100%)"></div>
  <div class="blog-body">
    <h3>FANTASY FOOTBALL</h3>
    <div class="meta"><span><svg width="12" height="12" viewBox="0 0 12 12"><rect x="1" y="2" width="10" height="9" fill="none" stroke="#555"/><path d="M1 5h10" stroke="#555"/></svg>March 25, 2015</span><i class="sep"></i><span><svg width="12" height="12" viewBox="0 0 12 12"><path d="M1 2h10v6H5l-3 3V8H1z" fill="none" stroke="#555"/></svg>No comments</span><i class="sep"></i><span><svg width="12" height="12" viewBox="0 0 12 12"><path d="M2 10 9 3l1 1-7 7H2z" fill="#555"/></svg>Makeup</span></div>
    <p>Lorem ipsum dolor sit amet, consectetur adipiscing elit, sed do eiusmod tempor incididunt ut labore et dolore magna aliqua. Ut enim ad minim veniam, quis nostrud exercitation ullamco laboris nisi ut aliquip ex ea commodo consequat. r</p>
    <div class="cats"><b>CATEGORIES :</b>Fantasy football , World's Worst , ween, wellhead</div>
    <div class="more">CLICK HERE &gt;&gt;</div>
  </div>
</article>

<article class="blog-card" style="top:1339px">
  <div class="photo" role="img" aria-label="Player in green number 31 jersey raising a football in a stadium" style="background:linear-gradient(180deg,#4a4a52 0%,#7a6a55 35%,#2f6a3a 65%,#3b5a30 100%)"></div>
  <div class="blog-body">
    <h3>FANTASY FOOTBALL</h3>
    <div class="meta"><span><svg width="12" height="12" viewBox="0 0 12 12"><rect x="1" y="2" width="10" height="9" fill="none" stroke="#555"/><path d="M1 5h10" stroke="#555"/></svg>March 25, 2015</span><i class="sep"></i><span><svg width="12" height="12" viewBox="0 0 12 12"><path d="M1 2h10v6H5l-3 3V8H1z" fill="none" stroke="#555"/></svg>No comments</span><i class="sep"></i><span><svg width="12" height="12" viewBox="0 0 12 12"><path d="M2 10 9 3l1 1-7 7H2z" fill="#555"/></svg>Makeup</span></div>
    <p>Lorem ipsum dolor sit amet, consectetur adipiscing elit, sed do eiusmod tempor incididunt ut labore et dolore magna aliqua. Ut enim ad minim veniam, quis nostrud exercitation ullamco laboris nisi ut aliquip ex ea commodo consequat. r</p>
    <div class="cats"><b>CATEGORIES :</b>Fantasy football , World's Worst , ween, wellhead</div>
    <div class="more">CLICK HERE &gt;&gt;</div>
  </div>
</article>

<article class="blog-card" style="top:1630px">
  <div class="photo" role="img" aria-label="Player in red number 29 jersey at the line of scrimmage" style="background:linear-gradient(180deg,#3b2f2e 0%,#7a3232 40%,#a52a2e 60%,#4f6a3a 100%)"></div>
  <div class="blog-body">
    <h3>FANTASY FOOTBALL</h3>
    <div class="meta"><span><svg width="12" height="12" viewBox="0 0 12 12"><rect x="1" y="2" width="10" height="9" fill="none" stroke="#555"/><path d="M1 5h10" stroke="#555"/></svg>March 25, 2015</span><i class="sep"></i><span><svg width="12" height="12" viewBox="0 0 12 12"><path d="M1 2h10v6H5l-3 3V8H1z" fill="none" stroke="#555"/></svg>No comments</span><i class="sep"></i><span><svg width="12" height="12" viewBox="0 0 12 12"><path d="M2 10 9 3l1 1-7 7H2z" fill="#555"/></svg>Makeup</span></div>
    <p>Lorem ipsum dolor sit amet, consectetur adipiscing elit, sed do eiusmod tempor incididunt ut labore et dolore magna aliqua. Ut enim ad minim veniam, quis nostrud exercitation ullamco laboris nisi ut aliquip ex ea commodo consequat. r</p>
    <div class="cats"><b>CATEGORIES :</b>Fantasy football , World's Worst , ween, wellhead</div>
    <div class="more">CLICK HERE &gt;&gt;</div>
  </div>
</article>

<h2 class="section-title" style="left:98px;top:1916px">FEATURED VIDEO</h2>
<div class="video-main">
  <div class="photo" role="img" aria-label="Player in navy number 31 jersey holding a football in a stadium at dusk" style="left:0;top:0;width:337px;height:263px;background:linear-gradient(180deg,#5a5040 0%,#8a7050 30%,#2c3550 60%,#3d5a2e 100%)"></div>
  <div class="video-caption">2014 QWR FREE AGENT RUNNING BACKS</div>
</div>
<div class="video-thumb photo" role="img" aria-label="Quarterback throwing on the field" style="left:459px;top:1966px;background:linear-gradient(180deg,#6a7a55,#4f7d36)"></div>
<div class="video-thumb photo" role="img" aria-label="Lineman in a three point stance" style="left:638px;top:1966px;background:linear-gradient(180deg,#2a2a2a,#6a2a2a 60%,#3a5a2a)"></div>
<div class="thumb-cap" style="left:459px;top:2077px">Few- QWR players who NBS...</div>
<div class="thumb-cap" style="left:638px;top:2077px">Few- QWR players who NBS...</div>
<div class="video-thumb photo" role="img" aria-label="Players tackling on green turf" style="left:459px;top:2103px;background:linear-gradient(180deg,#3f7a35,#4f8a3c)"></div>
<div class="video-thumb photo" role="img" aria-label="Running back breaking a tackle" style="left:638px;top:2103px;background:linear-gradient(180deg,#4a6a3a,#8a5a3a 55%,#3f6a30)"></div>
<div class="thumb-cap" style="left:459px;top:2214px">Few- QWR players who NBS...</div>
<div class="thumb-cap" style="left:638px;top:2214px">Few- QWR players who NBS...</div>

<h3 class="side-title" style="top:740px">PLAYER NEWS</h3>
<div class="news-item" style="top:802px"><div class="photo" role="img" aria-label="Player action shot" style="background:linear-gradient(180deg,#5a6a4a,#4a7a34)"></div><div class="nt">Team I Player Name I QB</div><div class="nd">2014 QWR Free Agent WRs Rising and Falling on New Teams Trouble Brewing</div></div>
<div class="news-item" style="top:905px"><div class="photo" role="img" aria-label="Player action shot" style="background:linear-gradient(180deg,#5a6a4a,#4a7a34)"></div><div class="nt">Team I Player Name I QB</div><div class="nd">2014 QWR Free Agent WRs Rising and Falling on New Teams Trouble Brewing</div></div>
<div class="news-item" style="top:1008px"><div class="photo" role="img" aria-label="Player action shot" style="background:linear-gradient(180deg,#5a6a4a,#4a7a34)"></div><div class="nt">Team I Player Name I QB</div><div class="nd">2014 QWR Free Agent WRs Rising and Falling on New Teams Trouble Brewing</div></div>
<div class="news-item" style="top:1111px"><div class="photo" role="img" aria-label="Player in dark jersey running with the ball" style="background:linear-gradient(180deg,#2a3048,#5a4a3a)"></div><div class="nt">Team I Player Name I QB</div><div class="nd">2014 QWR Free Agent WRs Rising and Falling on New Teams Trouble Brewing</div></div>

<div class="ad photo" role="img" aria-label="Audiobook advertisement with earbuds and a row of book covers: Download a free audiobook, 150,000+ audiobooks and more, works with your smartphone and tablet, from Listenly" style="top:1214px;height:272px;background:linear-gradient(180deg,#f4f4f4 0%,#eaeaea 55%,#8a6a55 78%,#5a4a40 100%)"></div>

<h3 class="side-title" style="top:1508px">FANTASY OFFSEASON 2014</h3>
<div class="off-item" style="top:1556px"><div class="photo" role="img" aria-label="Player in dark jersey" style="background:linear-gradient(180deg,#2a3048,#5a4a3a)"></div><div class="nd">2014 QWR Free Agent WRs Rising and Falling on New Teams Trouble Brewing 2014 QWR Free</div></div>
<div class="off-item" style="top:1650px"><div class="photo" role="img" aria-label="Players on the field" style="background:linear-gradient(180deg,#5a6a4a,#4a7a34)"></div><div class="nd">2014 QWR Free Agent WRs Rising and Falling on New Teams Trouble Brewing 2014 QWR Free</div></div>
<div class="off-item" style="top:1744px"><div class="photo" role="img" aria-label="Running back with the ball" style="background:linear-gradient(180deg,#4a6a3a,#8a5a3a 55%,#3f6a30)"></div><div class="nd">2014 QWR Free Agent WRs Rising and Falling on New Teams Trouble Brewing 2014 QWR Free</div></div>

<div class="ad photo" role="img" aria-label="Used motorcycle marketplace advertisement showing four bikes: Ranger 350 cc, Kestrel RR 250, Vento X1, Drift Voyager, with Great Deal on Used Bikes, buy or sell now, www.swapnest.com" style="top:1856px;height:273px;background:linear-gradient(180deg,#ffffff 0%,#f1f1f1 70%,#e6f0d8 100%);border:1px solid var(--line)"></div>

<div class="social-btn" style="left:836px;background:#3a5a98"><i></i>Friendwall</div>
<div class="social-btn" style="left:902px;background:#3aaee0"><i></i>Chirpr</div>
<div class="social-btn" style="left:968px;background:#2a6aa0"><i></i>Linkwork</div>
<div class="social-btn" style="left:1034px;background:#c4161c"><i></i>ClipTube</div>

<footer class="site-footer">
  <div class="f-col" style="left:98px;width:250px">
    <h4>ABOUT US</h4>
    <p>Lorem ipsum dolor sit amet, consectetur adip-isicing elit, sed do eiusmod tempor incididunt ut labore et dolore magna aliqua. Ut enim ad minim veniam, quis nostrud exercitation ullamco laboris nisi ut aliquip</p>
  </div>
  <div class="f-col" style="left:391px;width:250px">
    <h4>CONTACT US</h4>
    <p style="font-size:12.5px;color:#bbb">14 Kickoff Row, Fieldham Lane<br>Ashby AB3 9QT</p>
    <div class="contact-row" style="margin-top:14px"><svg width="18" height="16" viewBox="0 0 18 16"><path d="M4 1 7 4 5 6c1 2 3 4 5 5l2-2 3 3-2 3C8 15 2 9 1 4z" fill="none" stroke="#aaa" stroke-width="1.3"/></svg>+44 20 5550 0147</div>
    <div class="contact-row"><svg width="18" height="14" viewBox="0 0 18 14"><rect x="1" y="1" width="16" height="12" fill="none" stroke="#aaa" stroke-width="1.3"/><path d="m1 1 8 7 8-7" fill="none" stroke="#aaa" stroke-width="1.3"/></svg>info@endzone-oracle.com</div>
  </div>
  <div class="f-col" style="left:686px;width:270px">
    <h4>NEWSLETTER</h4>
    <p style="font-size:11px">Excepteur sint occaecat cupidatat non proident, sunt in culpa qui officia deserunt mollit anim</p>
    <div class="newsletter"><input type="text" value="Enter your email address"><button>Sign Up</button></div>
  </div>
  <div class="f-col" style="left:1011px;top:30px;width:110px">
    <h4>SOCIAL</h4>
    <ul class="social-list">
      <li><i></i>Friendwall</li>
      <li><i></i>Chirpr</li>
      <li><i></i>Circlenet</li>
      <li><i></i>ClipTube</li>
    </ul>
  </div>
  <div class="f-rule"></div>
  <div class="copyright">© 2015 Endzone Oracle - All Rights Reserved</div>
</footer>

</body>
</html>
```